Vehicle Rental Hire in the Algarve - Portugal

We are opening a Vehicle Rental company in the Algarve - Portugal - this will attract both locals and Tourists visiting. So we want this website to capture the beautiful location we will be set in, along with the familiarity of a vehicle rental company. And to keep a colour scheme in Line with out Logo. We are Quenmira Vehicle Rental.

Industry/Entity Type

Vehicle Rental

Number of Pages Required

1 page

Requirements
Must have
• must be professional, and simple to use navigation bar - must also have a "make a reservation" box - similar to the screenshot attached - Under our logo it must read "Vehicle Rental"
Nice to have
• It needs to be in a colour scheme that fits in with our logo

```html
<!DOCTYPE html>
<html lang="en">
<head>
<meta charset="utf-8">
<title>Quenmira Vehicle Rental</title>
<link href="https://fonts.googleapis.com/css2?family=Poppins:wght@400;500;600;700;800&display=swap" rel="stylesheet">
<style>
:root{
  --stage:#4d4d4d;
  --blue:#1c12dd;
  --blue-soft:#3d35e8;
  --red:#d22d2b;
  --band-red:#c42f28;
  --lilac:#b8b2f4;
  --page:#f4f4f6;
  --mist:#eeedfa;
  --panel:#ececf0;
  --ink:#141414;
  --muted:#8a8a92;
  --white:#ffffff;
}
*{box-sizing:border-box;margin:0;padding:0}
html,body{width:1200px;height:1200px;overflow:hidden}
body{background:var(--stage);font-family:'Poppins',sans-serif;color:var(--ink);position:relative}

.page{position:absolute;left:106px;top:38px;width:695px;height:1123px;background:var(--page);overflow:hidden}

/* header */
.site-header{position:absolute;left:0;top:0;width:100%;height:56px;background:var(--page)}
.brand{position:absolute;left:36px;top:10px;display:flex;align-items:center;gap:8px}
.brand-mark{width:58px;height:58px;border-radius:50%;background:var(--white);border:1.5px solid var(--blue);display:flex;align-items:center;justify-content:center;position:relative;z-index:3}
.brand-name{font-size:9px;font-weight:600;color:var(--blue)}
.brand-tag{font-size:12px;font-weight:500;color:var(--red)}
.lang{position:absolute;left:458px;top:25px;width:61px;height:16px;border:1px solid #bdbdc4;border-radius:3px;background:var(--white);font-size:7.5px;display:flex;align-items:center;padding-left:4px;gap:3px}
.lang .caret{border-left:2.5px solid transparent;border-right:2.5px solid transparent;border-top:4px solid #777;margin-left:2px}
.support{position:absolute;left:537px;top:22px;display:flex;gap:5px;align-items:flex-start}
.support-label{font-size:7.5px;font-weight:500;line-height:1.2}
.support-phone{font-size:12px;color:var(--blue);font-weight:500;line-height:1.3}

.main-nav{position:absolute;left:0;top:56px;width:100%;height:33px;background:var(--blue);z-index:1}
.main-nav a{position:absolute;top:0;height:33px;line-height:33px;font-size:7.5px;color:var(--white);text-decoration:none;transform:translateX(-50%)}
.main-nav a.active{background:var(--blue-soft);width:37px;text-align:center;font-weight:600}

/* hero */
.hero{position:absolute;left:0;top:89px;width:100%;height:336px;
  background:
   radial-gradient(ellipse 220px 140px at 95% 5%,#3e7f96 0%,rgba(62,127,150,0) 100%),
   radial-gradient(ellipse 260px 160px at 38% 38%,#cfc3bb 0%,rgba(207,195,187,0) 100%),
   linear-gradient(160deg,#4e5a2f 0%,#7c6a44 35%,#b77b57 60%,#d7ad86 100%)}
.hero-title{position:absolute;left:37px;top:225px;font-size:34px;line-height:50px;font-weight:800;color:var(--white);letter-spacing:-.3px}

/* reservation */
.reservation{position:absolute;width:203px;border:4px solid var(--lilac);border-bottom:none;border-radius:20px 20px 0 0;background:rgba(236,236,240,.94);padding:0 18px}
.reservation h3{font-size:11px;font-weight:600;text-align:center;margin:24px 0 16px}
.field{height:24px;background:var(--white);border-radius:2px;display:flex;align-items:center;padding:0 6px;gap:5px;position:relative}
.field::after{content:"";position:absolute;right:7px;top:10px;border-left:2.5px solid transparent;border-right:2.5px solid transparent;border-top:4px solid #444}
.field .ph{font-size:6.5px;color:var(--muted)}
.field .stack{display:flex;flex-direction:column;line-height:1.15}
.field .tiny{font-size:4.3px;color:var(--muted)}
.field .val{font-size:6.5px}
.split{display:flex;gap:2px}
.split .field:first-child{flex:1.45}
.split .field:last-child{flex:1}
.check{display:flex;align-items:center;gap:5px;font-size:6.5px;height:17px;padding-left:6px}
.check .box{width:7px;height:7px;border-radius:1.5px;background:#d0d0d6}
.check .box.on{background:var(--blue-soft)}
.rows{display:flex;flex-direction:column;gap:7px}
.search-btn{display:block;width:100%;height:26px;margin-top:4px;background:var(--blue);color:var(--white);border:none;border-radius:2px;font-family:'Poppins',sans-serif;font-size:8px;font-weight:600}

/* promo section */
.promo{position:absolute;left:0;top:410px;width:100%;height:236px;background:var(--mist);border-radius:31px 31px 0 0}
.promo-banner{position:absolute;left:93px;top:36px;width:508px;height:140px;border-radius:10px;
  background:linear-gradient(100deg,#2e1c12 0%,#5b3520 40%,#a56b3e 75%,#6f7079 100%)}
.promo-title{position:absolute;left:17px;top:10px;font-size:21px;line-height:33px;font-weight:700;color:var(--white)}
.newsletter{position:absolute;left:420px;top:125px;width:199px;height:72px;background:var(--page);border-radius:6px;padding:10px 11px}
.newsletter h4{font-size:8.5px;font-weight:600;color:var(--blue-soft)}
.newsletter p{font-size:6.5px;color:var(--blue-soft);margin-top:1px}
.newsletter .row{display:flex;gap:5px;margin-top:4px}
.newsletter .email{flex:1;height:25px;background:var(--white);border:1px solid #e2e2e8;border-radius:2px;font-size:6.5px;color:var(--muted);padding-left:7px;line-height:23px}
.newsletter .send{width:26px;height:25px;background:var(--blue);border-radius:2px;display:flex;align-items:center;justify-content:center}

/* categories */
.categories{position:absolute;left:0;top:646px;width:100%;height:290px;background:var(--page)}
.categories h2{position:absolute;left:37px;top:36px;font-size:16px;font-weight:600;color:#6b6b70}
.categories h2 span{color:var(--blue-soft)}
.car-card{position:absolute;top:72px;width:107px;height:177px;background:var(--white);border-radius:8px;padding:0 7px}
.car-photo{height:72px;margin:6px 0 8px;border-radius:4px;background:radial-gradient(ellipse 48% 34% at 50% 55%,#cfd2d8 0%,#eef0f3 70%,#ffffff 100%)}
.car-type{font-size:5.5px;color:var(--red)}
.car-name{font-size:7px;font-weight:500;white-space:nowrap}
.car-name small{font-size:4.3px;color:var(--muted);font-weight:400}
.specs{display:flex;gap:8px;font-size:5px;margin-top:9px;align-items:center}
.specs i{display:inline-block;width:6px;height:5px;background:var(--ink);border-radius:1px;margin-right:1px;vertical-align:-1px}
.specs + .specs{margin-top:5px}
.book-btn{display:block;width:100%;height:18px;margin-top:11px;border:1px solid #bdbdc4;border-radius:3px;background:var(--white);font-family:'Poppins',sans-serif;font-size:6.5px;font-weight:600}
.price{text-align:center;font-size:3.8px;color:var(--blue);margin-top:3px}
.price b{font-size:5.5px;font-weight:600}

/* footer */
.site-footer{position:absolute;left:0;top:936px;width:100%;height:154px;background:var(--mist)}
.foot-brand{position:absolute;left:37px;top:20px;width:62px;text-align:center}
.foot-mark{width:26px;height:26px;margin:0 auto;border-radius:50%;border:1px solid var(--blue);display:flex;align-items:center;justify-content:center;font-size:4.5px;color:var(--blue);font-weight:600}
.foot-brand .brand-tag{font-size:8px;margin-top:3px;display:block}
.contact{position:absolute;left:37px;top:70px;font-size:6.5px;line-height:11.5px}
.contact h5{font-size:7.5px;font-weight:600;margin-bottom:2px}
.foot-links{position:absolute;left:241px;top:22px;width:200px;text-align:center}
.foot-links h5{font-size:8px;font-weight:500}
.foot-links nav{display:flex;justify-content:center;gap:11px;font-size:7px;margin-top:6px}
.foot-links nav a{color:var(--ink);text-decoration:none}
.foot-links nav a.active{font-weight:600}
.social{position:absolute;top:21px;width:15px;height:15px;border-radius:50%;background:var(--blue-soft)}
.rule{position:absolute;left:37px;top:132px;width:621px;height:1px;background:#9a9aa3}
.copyright{position:absolute;left:0;top:1090px;width:100%;height:33px;background:var(--band-red);color:var(--white);font-size:7.5px;text-align:center;line-height:33px}
</style>
</head>
<body>

<main class="page">
  <header class="site-header">
    <div class="brand">
      <div class="brand-mark"><span class="brand-name">Quenmira</span></div>
      <span class="brand-tag">Vehicle Rental</span>
    </div>
    <div class="lang">English
      <svg width="12" height="8" viewBox="0 0 12 8"><rect width="12" height="8" fill="#24307a"/><path d="M0 0L12 8M12 0L0 8" stroke="#fff" stroke-width="1.6"/><path d="M6 0V8M0 4H12" stroke="#fff" stroke-width="2.4"/><path d="M6 0V8M0 4H12" stroke="#c8102e" stroke-width="1.2"/></svg>
      <span class="caret"></span>
    </div>
    <div class="support">
      <svg width="25" height="23" viewBox="0 0 25 23"><path d="M3 1h19a2 2 0 0 1 2 2v13a2 2 0 0 1-2 2H10l-5 4v-4H3a2 2 0 0 1-2-2V3a2 2 0 0 1 2-2z" fill="#111"/><path d="M8 5c1 4 4 7 8 8l1.5-1.8-2.3-1.5-1 1c-1.4-.6-2.6-1.8-3.2-3.2l1-1L10.5 4z" fill="#fff"/></svg>
      <div>
        <div class="support-label">Customer Support</div>
        <div class="support-phone">+351 289 000 417</div>
      </div>
    </div>
  </header>

  <nav class="main-nav">
    <a class="active" href="#" style="left:240px">Home</a>
    <a href="#" style="left:304px">Fleet</a>
    <a href="#" style="left:372px">Services</a>
    <a href="#" style="left:448px">Contacts</a>
  </nav>

  <section class="hero" role="img" aria-label="Aerial photo of a whitewashed Algarve village above a sandy beach and the Atlantic coast">
  </section>
  <h1 class="hero-title" style="position:absolute;top:314px;left:37px">BEST VEHICLE RENTAL<br>IN ALGARVE</h1>

  <form class="reservation" style="left:426px;top:128px;height:282px">
    <h3>Make a Reservation</h3>
    <div class="rows">
      <div class="field"><svg width="7" height="8" viewBox="0 0 7 8"><path d="M3.5 7.5S1 4.8 1 3a2.5 2.5 0 0 1 5 0c0 1.8-2.5 4.5-2.5 4.5z" fill="none" stroke="#d22d2b" stroke-width=".8"/><circle cx="3.5" cy="3" r=".9" fill="none" stroke="#d22d2b" stroke-width=".7"/></svg><span class="ph">Pick up location</span></div>
      <label class="check"><span class="box"></span>Return to different location</label>
      <div class="split">
        <div class="field"><svg width="7" height="7" viewBox="0 0 7 7"><rect x=".5" y="1" width="6" height="5.5" fill="none" stroke="#d22d2b" stroke-width=".7"/><path d="M.5 2.8h6" stroke="#d22d2b" stroke-width=".7"/></svg><div class="stack"><span class="tiny">Pick up date</span><span class="val">dd-mm-aaaa</span></div></div>
        <div class="field"><svg width="7" height="7" viewBox="0 0 7 7"><circle cx="3.5" cy="3.5" r="3" fill="none" stroke="#d22d2b" stroke-width=".7"/><path d="M3.5 1.8v1.7l-1 .9" fill="none" stroke="#d22d2b" stroke-width=".7"/></svg><div class="stack"><span class="tiny">Hour</span><span class="val">10:00</span></div></div>
      </div>
      <div class="split">
        <div class="field"><svg width="7" height="7" viewBox="0 0 7 7"><rect x=".5" y="1" width="6" height="5.5" fill="none" stroke="#d22d2b" stroke-width=".7"/><path d="M.5 2.8h6" stroke="#d22d2b" stroke-width=".7"/></svg><div class="stack"><span class="tiny">Drop off date</span><span class="val">dd-mm-aaaa</span></div></div>
        <div class="field"><svg width="7" height="7" viewBox="0 0 7 7"><circle cx="3.5" cy="3.5" r="3" fill="none" stroke="#d22d2b" stroke-width=".7"/><path d="M3.5 1.8v1.7l-1 .9" fill="none" stroke="#d22d2b" stroke-width=".7"/></svg><div class="stack"><span class="tiny">Hour</span><span class="val">10:00</span></div></div>
      </div>
      <div class="field"><svg width="7" height="7" viewBox="0 0 7 7"><circle cx="3.5" cy="2.2" r="1.6" fill="none" stroke="#d22d2b" stroke-width=".7"/><path d="M.6 6.6c.4-1.7 1.5-2.5 2.9-2.5s2.5.8 2.9 2.5z" fill="none" stroke="#d22d2b" stroke-width=".7"/></svg><div class="stack"><span class="tiny">Driver's age</span><span class="val">27</span></div></div>
      <div class="field"><svg width="8" height="6" viewBox="0 0 8 6"><path d="M1 4V2.8L2 1h4l1 1.8V4zM1 4v1.5h1.3V4M5.7 4v1.5H7V4" fill="none" stroke="#d22d2b" stroke-width=".7"/></svg><div class="stack"><span class="tiny">Vehicle Category</span><span class="val">All</span></div></div>
      <button class="search-btn" type="button">Search</button>
    </div>
  </form>

  <section class="promo">
    <div class="promo-banner" role="img" aria-label="Photo of a white hatchback driving along a coastal road at sunset">
      <h2 class="promo-title">Book the Affordable<br>Car Rental Easily</h2>
    </div>
    <div class="newsletter">
      <h4>Newsletter</h4>
      <p>Subscribe our news</p>
      <div class="row">
        <div class="email">Write your email</div>
        <div class="send"><svg width="9" height="9" viewBox="0 0 9 9"><rect x=".5" y=".5" width="8" height="8" rx="1" fill="#fff"/><path d="M6.8 2.2L2.2 4.4l2 .5.5 2z" fill="#1c12dd"/></svg></div>
      </div>
    </div>
  </section>

  <section class="categories">
    <h2><span>Vehicle Category.</span> Choose the best suited car for you</h2>

    <article class="car-card" style="left:37px">
      <div class="car-photo" role="img" aria-label="White economy hatchback"></div>
      <div class="car-type">Economy</div>
      <div class="car-name">Corvale Hatch <small>or similar</small></div>
      <div class="specs"><span><i></i>5</span><span><i></i>5</span><span><i></i>5</span></div>
      <div class="specs"><span><i></i>Petrol</span><span><i></i>Automatic</span></div>
      <button class="book-btn" type="button">Book Now</button>
      <div class="price">Start from <b>€20.00</b></div>
    </article>

    <article class="car-card" style="left:155px">
      <div class="car-photo" role="img" aria-label="Dark blue compact SUV" style="background:radial-gradient(ellipse 48% 34% at 50% 55%,#5a6a85 0%,#e6e9ef 70%,#fff 100%)"></div>
      <div class="car-type">Automatic</div>
      <div class="car-name">Rendra Kasso <small>or similar</small></div>
      <div class="specs"><span><i></i>5</span><span><i></i>5</span><span><i></i>5</span></div>
      <div class="specs"><span><i></i>Petrol</span><span><i></i>Manual</span></div>
      <button class="book-btn" type="button">Book Now</button>
      <div class="price">Start from <b>€20.00</b></div>
    </article>

    <article class="car-card" style="left:273px">
      <div class="car-photo" role="img" aria-label="Silver seven seater SUV" style="background:radial-gradient(ellipse 48% 34% at 50% 55%,#9b9ea3 0%,#eceef1 70%,#fff 100%)"></div>
      <div class="car-type">7 Seater</div>
      <div class="car-name">Nirova Trail <small>or similar</small></div>
      <div class="specs"><span><i></i>7</span><span><i></i>5</span><span><i></i>2</span></div>
      <div class="specs"><span><i></i>Petrol</span><span><i></i>Manual</span></div>
      <button class="book-btn" type="button">Book Now</button>
      <div class="price">Start from <b>€20.00</b></div>
    </article>

    <article class="car-card" style="left:392px">
      <div class="car-photo" role="img" aria-label="Silver compact hatchback" style="background:radial-gradient(ellipse 48% 34% at 50% 55%,#b4b7bc 0%,#eef0f3 70%,#fff 100%)"></div>
      <div class="car-type">Compact</div>
      <div class="car-name">Pelano Two <small>or similar</small></div>
      <div class="specs"><span><i></i>5</span><span><i></i>5</span><span><i></i>3</span></div>
      <div class="specs"><span><i></i>Petrol</span><span><i></i>Manual</span></div>
      <button class="book-btn" type="button">Book Now</button>
      <div class="price">Start from <b>€20.00</b></div>
    </article>

    <article class="car-card" style="left:510px">
      <div class="car-photo" role="img" aria-label="White family estate car"></div>
      <div class="car-type">Family</div>
      <div class="car-name">Pelano Estate <small>or similar</small></div>
      <div class="specs"><span><i></i>5</span><span><i></i>5</span><span><i></i>5</span></div>
      <div class="specs"><span><i></i>Petrol</span><span><i></i>Manual</span></div>
      <button class="book-btn" type="button">Book Now</button>
      <div class="price">Start from <b>€20.00</b></div>
    </article>

    <article class="car-card" style="left:628px">
      <div class="car-photo" role="img" aria-label="White nine seat minibus"></div>
      <div class="car-type">Minibus</div>
      <div class="car-name">Pelano Voyager <small>or similar</small></div>
      <div class="specs"><span><i></i>9</span><span><i></i>5</span><span><i></i>5</span></div>
      <div class="specs"><span><i></i>Diesel</span><span><i></i>Manual</span></div>
      <button class="book-btn" type="button">Book Now</button>
      <div class="price">Start from <b>€20.00</b></div>
    </article>
  </section>

  <footer class="site-footer">
    <div class="foot-brand">
      <div class="foot-mark">Quenmira</div>
      <span class="brand-tag">Vehicle Rental</span>
    </div>
    <div class="contact">
      <h5>General Contact</h5>
      <div>Address</div>
      <div>email@mail.com</div>
      <div>Phone number</div>
    </div>
    <div class="foot-links">
      <h5>Links</h5>
      <nav><a class="active" href="#">Home</a><a href="#">Fleet</a><a href="#">Services</a><a href="#">Contacts</a></nav>
    </div>
    <span class="social" style="left:584px"></span>
    <span class="social" style="left:613px"></span>
    <span class="social" style="left:643px"></span>
    <div class="rule"></div>
  </footer>
  <div class="copyright">Copyright © 2024 - <b style="font-weight:500">QUENMIRA LIMITADA</b>. all right reserved</div>
</main>

<form class="reservation" style="left:894px;top:135px;height:326px">
  <h3>Make a Reservation</h3>
  <div class="rows">
    <div class="field"><svg width="7" height="8" viewBox="0 0 7 8"><path d="M3.5 7.5S1 4.8 1 3a2.5 2.5 0 0 1 5 0c0 1.8-2.5 4.5-2.5 4.5z" fill="none" stroke="#d22d2b" stroke-width=".8"/><circle cx="3.5" cy="3" r=".9" fill="none" stroke="#d22d2b" stroke-width=".7"/></svg><span class="ph">Pick up location</span></div>
    <label class="check"><span class="box on"></span>Return to different location</label>
    <div class="field"><svg width="7" height="8" viewBox="0 0 7 8"><path d="M3.5 7.5S1 4.8 1 3a2.5 2.5 0 0 1 5 0c0 1.8-2.5 4.5-2.5 4.5z" fill="none" stroke="#d22d2b" stroke-width=".8"/><circle cx="3.5" cy="3" r=".9" fill="none" stroke="#d22d2b" stroke-width=".7"/></svg><span class="ph">Drop off location</span></div>
    <div class="split">
      <div class="field"><svg width="7" height="7" viewBox="0 0 7 7"><rect x=".5" y="1" width="6" height="5.5" fill="none" stroke="#d22d2b" stroke-width=".7"/><path d="M.5 2.8h6" stroke="#d22d2b" stroke-width=".7"/></svg><div class="stack"><span class="tiny">Pick up date</span><span class="val">dd-mm-aaaa</span></div></div>
      <div class="field"><svg width="7" height="7" viewBox="0 0 7 7"><circle cx="3.5" cy="3.5" r="3" fill="none" stroke="#d22d2b" stroke-width=".7"/><path d="M3.5 1.8v1.7l-1 .9" fill="none" stroke="#d22d2b" stroke-width=".7"/></svg><div class="stack"><span class="tiny">Hour</span><span class="val">10:00</span></div></div>
    </div>
    <div class="split">
      <div class="field"><svg width="7" height="7" viewBox="0 0 7 7"><rect x=".5" y="1" width="6" height="5.5" fill="none" stroke="#d22d2b" stroke-width=".7"/><path d="M.5 2.8h6" stroke="#d22d2b" stroke-width=".7"/></svg><div class="stack"><span class="tiny">Drop off date</span><span class="val">dd-mm-aaaa</span></div></div>
      <div class="field"><svg width="7" height="7" viewBox="0 0 7 7"><circle cx="3.5" cy="3.5" r="3" fill="none" stroke="#d22d2b" stroke-width=".7"/><path d="M3.5 1.8v1.7l-1 .9" fill="none" stroke="#d22d2b" stroke-width=".7"/></svg><div class="stack"><span class="tiny">Hour</span><span class="val">10:00</span></div></div>
    </div>
    <div class="field"><svg width="7" height="7" viewBox="0 0 7 7"><circle cx="3.5" cy="2.2" r="1.6" fill="none" stroke="#d22d2b" stroke-width=".7"/><path d="M.6 6.6c.4-1.7 1.5-2.5 2.9-2.5s2.5.8 2.9 2.5z" fill="none" stroke="#d22d2b" stroke-width=".7"/></svg><div class="stack"><span class="tiny">Driver's age</span><span class="val">27</span></div></div>
    <div class="field"><svg width="8" height="6" viewBox="0 0 8 6"><path d="M1 4V2.8L2 1h4l1 1.8V4zM1 4v1.5h1.3V4M5.7 4v1.5H7V4" fill="none" stroke="#d22d2b" stroke-width=".7"/></svg><div class="stack"><span class="tiny">Vehicle Category</span><span class="val">All</span></div></div>
    <button class="search-btn" type="button">Search</button>
  </div>
</form>

</body>
</html>
```